Charity Initiative needs a WebPage design

We need a web design for charity initiative by two young guys riding their bikes around Australia to support HarbourLight which helps people with depression and anxiety. Full brief and requirements are attached in the PDF and word document. We have the logo already done and attached. Website will be done in Wordpress and need to get Donations, display current donations, show live Video feed, GPS tracker, Blogs etc and also ability to sell merchandise later

Target Market(s)

Sponsors, Business, Young People

Number of Pages Required

4 page

Font styles to use
Serif
Sans Serif
Decorative
Script

Requirements
Must have
• As per Brief and also Donation status etc
Nice to have
• Please check my logo and read the Bried

```html
<!DOCTYPE html>
<html lang="en">
<head>
<meta charset="utf-8">
<title>Open Road Ride</title>
<link rel="stylesheet" href="https://fonts.googleapis.com/css2?family=Raleway:wght@400;500;600;700;800&family=Open+Sans:wght@400;600&display=swap">
<style>
:root{
  --white:#ffffff;
  --ink:#2b2b2b;
  --body:#6a6a6a;
  --muted:#8a8a8a;
  --orange:#f05a28;
  --pink:#e8286a;
  --red-link:#e0452a;
  --yellow:#f0b400;
  --nav-top:#f9c21a;
  --nav-bottom:#eea708;
  --teal:#3fb0aa;
  --teal-dark:#2c9590;
  --teal-bar:#4cc4bf;
  --btn-teal:#2aa3a0;
  --feed-bg:#f4efef;
  --tan:#e9d7c2;
  --bar-track:#ffffff;
}
*{box-sizing:border-box;margin:0;padding:0}
html,body{width:1200px;height:2400px;overflow:hidden;background:var(--white)}
body{position:relative;font-family:'Open Sans',Arial,sans-serif;color:var(--body)}
h1,h2,h3,h4{font-family:'Raleway',Arial,sans-serif;font-weight:500;color:var(--ink)}

/* header */
.site-header{position:absolute;left:0;top:0;width:1200px;height:118px;background:var(--white)}
.brand{position:absolute;left:160px;top:34px;display:flex;align-items:center;gap:14px}
.brand-dot{width:44px;height:44px;border-radius:50%;background:var(--pink)}
.brand-name{font-family:'Raleway',sans-serif;font-weight:800;font-size:34px;color:var(--pink);letter-spacing:.5px}
.search{position:absolute;left:822px;top:70px;width:231px;height:33px;border:1px solid #cfcfcf;background:#fafafa;font-size:11px;color:#9a9a9a;padding:8px 12px}
.search svg{position:absolute;right:10px;top:8px}

/* nav */
.main-nav{position:absolute;left:0;top:118px;width:1200px;height:48px;background:linear-gradient(var(--nav-top),var(--nav-bottom));display:flex;padding-left:149px}
.main-nav a{display:block;height:48px;line-height:48px;padding:0 34px;color:var(--white);font-family:'Raleway',sans-serif;font-weight:600;font-size:16px;text-decoration:none;border-right:1px solid rgba(255,255,255,.25)}
.main-nav a.active{background:var(--orange);padding:0 36px;border-right:none}

/* hero */
.hero{position:absolute;left:0;top:166px;width:1200px;height:439px;background:linear-gradient(100deg,#f2642a 0%,#ee4a44 45%,#e62e67 100%);text-align:center;color:var(--white)}
.hero-photo{position:absolute;inset:0;background:radial-gradient(ellipse at 50% 55%,rgba(120,30,40,.25),rgba(0,0,0,0) 60%)}
.hero h1{position:absolute;left:0;right:0;top:136px;color:var(--white);font-weight:700;font-size:46px;letter-spacing:1px}
.hero h2{position:absolute;left:0;right:0;top:190px;color:var(--white);font-weight:700;font-size:37px;letter-spacing:1px}
.btn{display:inline-block;font-family:'Raleway',sans-serif;font-weight:600;color:var(--white);text-align:center}
.hero .btn{position:absolute;left:536px;top:246px;width:131px;height:35px;line-height:35px;font-size:14px;background:var(--btn-teal);box-shadow:0 2px 3px rgba(0,0,0,.2)}
.slider-dots{position:absolute;left:558px;top:397px;display:flex;gap:6px}
.slider-dots span{width:17px;height:17px;border-radius:50%;background:var(--white)}
.slider-dots span.current{background:transparent;border:2px solid var(--white)}

/* welcome */
.welcome{position:absolute;left:0;top:605px;width:1200px;height:328px;background:var(--white);overflow:hidden}
.welcome-deco{position:absolute;left:704px;top:0;width:496px;height:328px;background:radial-gradient(ellipse at 55% 50%,rgba(200,200,200,.45),rgba(230,230,230,.2) 55%,rgba(255,255,255,0) 72%)}
.welcome h2{position:absolute;left:148px;top:58px;font-size:29px;letter-spacing:.5px}
.welcome p{position:absolute;left:148px;width:560px;font-size:14px;line-height:24px}
.donations{position:absolute;left:757px;top:58px}
.donations h3{font-size:27px;letter-spacing:.5px}
.progress{position:absolute;left:1px;top:51px;width:301px;height:22px;border:3px solid var(--yellow);border-radius:12px;background:var(--bar-track);overflow:hidden}
.progress-fill{width:93%;height:100%;background:var(--pink);border-radius:8px 0 0 8px}
.ticks{position:absolute;left:10px;top:73px}
.amount{position:absolute;top:92px;font-size:14px;font-weight:600;color:var(--ink);font-family:Arial,sans-serif}
.donations .btn{position:absolute;left:5px;top:127px;width:137px;height:39px;line-height:39px;font-size:14px;background:var(--orange)}

/* video feeds */
.feeds{position:absolute;left:0;top:933px;width:1200px;height:355px;background:var(--feed-bg)}
.feeds h2{position:absolute;left:150px;top:40px;font-size:25px}
.feed{position:absolute;top:85px;width:206px}
.feed-thumb{width:206px;height:121px;border:3px solid var(--white);box-shadow:0 1px 3px rgba(0,0,0,.15);background:linear-gradient(160deg,#7a8a96,#3a3a3c 60%,#b23a3a);position:relative}
.feed-thumb .play{position:absolute;left:83px;top:40px}
.feed h4{font-family:'Open Sans',sans-serif;font-weight:400;font-size:15px;color:#555;margin-top:12px}
.feed p{font-size:12px;line-height:19px;color:var(--muted);margin-top:6px}
.feed .read{display:block;margin-top:15px;font-size:12px;color:var(--red-link);font-weight:600}

.divider-band{position:absolute;left:0;top:1288px;width:1200px;height:11px;background:var(--tan)}

/* highlights */
.highlights{position:absolute;left:0;top:1299px;width:1200px;height:298px;background:var(--yellow)}
.ring{position:absolute;width:184px;height:184px;border-radius:50%;border:2px solid rgba(255,255,255,.9);top:44px}
.ring-photo{position:absolute;left:7px;top:7px;width:166px;height:166px;border-radius:50%;border:3px solid var(--white)}
.highlight-text{position:absolute;top:56px;width:262px;color:var(--white)}
.highlight-text h3{color:var(--white);font-size:22px;line-height:28px;font-weight:500}
.highlight-text p{font-size:12px;line-height:17px;margin-top:10px;color:#fff6dc;width:236px}

/* blogs */
.blogs h2{position:absolute;left:148px;top:1666px;font-size:25px}
.post{position:absolute;left:149px;width:560px;height:116px}
.post-photo{position:absolute;left:0;top:0;width:179px;height:113px}
.post h4{position:absolute;left:195px;top:0;font-family:'Open Sans',sans-serif;font-weight:400;font-size:17px;color:#444}
.post p{position:absolute;left:195px;top:30px;width:370px;font-size:12.5px;line-height:20px;color:var(--muted)}
.post .read{position:absolute;left:195px;top:92px;font-size:14px;color:var(--pink);font-weight:600}

.gps{position:absolute;left:736px;top:1670px;width:320px;height:333px;border:1px solid #d8d8d8;background:var(--white)}
.gps-head{height:45px;line-height:45px;background:linear-gradient(var(--teal),var(--teal-dark));color:var(--white);font-family:'Raleway',sans-serif;font-weight:500;font-size:21px;padding-left:28px}
.gps-map{position:absolute;left:20px;top:62px;width:278px;height:252px;background:linear-gradient(135deg,#9cd8b0 0%,#4fb0bc 50%,#2f74bc 100%)}

/* footer */
.site-footer{position:absolute;left:0;top:2106px;width:1200px;height:232px;background:var(--teal)}
.footer-col{position:absolute;top:48px;color:var(--white)}
.footer-col h4{color:var(--white);font-family:'Raleway',sans-serif;font-weight:500;font-size:16px;margin-bottom:10px}
.footer-col li{list-style:none;font-size:12px;line-height:23px;color:#e8f7f6;display:flex;align-items:center;gap:6px}
.social{display:flex;gap:9px;margin-top:4px}
.social span{width:34px;height:34px;border-radius:50%;background:var(--teal-dark)}
.bottom-bar{position:absolute;left:0;top:2338px;width:1200px;height:62px;background:var(--teal-bar);font-size:11px;color:#e3f6f5;padding:27px 0 0 152px}
</style>
</head>
<body>

<header class="site-header">
  <div class="brand"><span class="brand-dot"></span><span class="brand-name">Open Road Ride</span></div>
  <div class="search">Search here
    <svg width="16" height="16" viewBox="0 0 16 16"><circle cx="6.5" cy="6.5" r="5" fill="none" stroke="#999" stroke-width="2"/><line x1="10.5" y1="10.5" x2="15" y2="15" stroke="#999" stroke-width="2"/></svg>
  </div>
</header>

<nav class="main-nav">
  <a class="active">HOME</a><a>ABOUT US</a><a>DONATION</a><a>GALLERY</a><a>BLOG</a><a>VIDEO</a><a style="border-right:none">RESOURCES</a>
</nav>

<section class="hero">
  <div class="hero-photo" role="img" aria-label="Two riders on dirt bikes racing along a dusty track, tinted orange to pink"></div>
  <h1>TWO MATES. TWO BIKES.</h1>
  <h2>ONE LONG ROAD</h2>
  <span class="btn">READ MORE</span>
  <div class="slider-dots"><span class="current"></span><span></span><span></span><span></span></div>
</section>

<section class="welcome">
  <div class="welcome-deco" role="img" aria-label="Faint silhouette of a rider on a motorbike"></div>
  <h2>WELCOME TO OPEN ROAD RIDE</h2>
  <p style="top:105px">Fusce ultricies orci ac feugiat suscipit leo massa sodales velit et scelerisque mi tortor at ipsum cligula augue bibendum accumsan vestibulum</p>
  <p style="top:166px">ut commodo a mi Morbi ornare gravida elit Integer congue augue et malesuada iaculis ipsum dui aliquet felis at cursus magna nisl nec elit Praesent elementum elit at tellus nec ultricies sit amet porttitor mattis enim In massa libero</p>
  <div class="donations">
    <h3>DONATIONS</h3>
    <div class="progress"><div class="progress-fill"></div></div>
    <svg class="ticks" width="280" height="10" viewBox="0 0 280 10"><g stroke="#888" stroke-width="1"><line x1="0" y1="0" x2="0" y2="8"/><line x1="28" y1="0" x2="28" y2="5"/><line x1="56" y1="0" x2="56" y2="5"/><line x1="84" y1="0" x2="84" y2="5"/><line x1="112" y1="0" x2="112" y2="5"/><line x1="140" y1="0" x2="140" y2="8"/><line x1="168" y1="0" x2="168" y2="5"/><line x1="196" y1="0" x2="196" y2="5"/><line x1="224" y1="0" x2="224" y2="5"/><line x1="252" y1="0" x2="252" y2="5"/><line x1="279" y1="0" x2="279" y2="8"/></g></svg>
    <span class="amount" style="left:6px">$0</span>
    <span class="amount" style="left:236px">$25.95</span>
    <span class="btn">DONATE NOW</span>
  </div>
</section>

<section class="feeds">
  <h2>VIDEO FEEDS</h2>
  <article class="feed" style="left:147px">
    <div class="feed-thumb" role="img" aria-label="Two riders on a red motorbike"><svg class="play" width="40" height="40" viewBox="0 0 40 40"><circle cx="20" cy="20" r="19" fill="#fff"/><path d="M15 11 L29 20 L15 29Z" fill="#222"/></svg></div>
    <h4>Praesent elementum elit</h4>
    <p>scelerisque mi tortor at ipsum cligula augue bibendum vestibulu</p>
    <span class="read">READ MORE</span>
  </article>
  <article class="feed" style="left:381px">
    <div class="feed-thumb" role="img" aria-label="Racer leaning into a corner on a track bike" style="background:linear-gradient(160deg,#9aa4a8,#5c6670 60%,#2a3a8a)"><svg class="play" width="40" height="40" viewBox="0 0 40 40"><circle cx="20" cy="20" r="19" fill="#fff"/><path d="M15 11 L29 20 L15 29Z" fill="#222"/></svg></div>
    <h4>Cum sociis natoqu</h4>
    <p>scelerisque mi tortor at ipsum cligula augue bibendum vestibulu</p>
    <span class="read">READ MORE</span>
  </article>
  <article class="feed" style="left:616px">
    <div class="feed-thumb" role="img" aria-label="Two riders with their motorbikes in a garage" style="background:linear-gradient(160deg,#6a4a3a,#2e2522 60%,#8a5a3a)"><svg class="play" width="40" height="40" viewBox="0 0 40 40"><circle cx="20" cy="20" r="19" fill="#fff"/><path d="M15 11 L29 20 L15 29Z" fill="#222"/></svg></div>
    <h4>Sed porta Suspendi</h4>
    <p>scelerisque mi tortor at ipsum cligula augue bibendum vestibulu</p>
    <span class="read">READ MORE</span>
  </article>
  <article class="feed" style="left:851px">
    <div class="feed-thumb" role="img" aria-label="Two touring riders on a tree-lined road" style="background:linear-gradient(160deg,#6d8a4a,#3c4a34 55%,#8a8a8a)"><svg class="play" width="40" height="40" viewBox="0 0 40 40"><circle cx="20" cy="20" r="19" fill="#fff"/><path d="M15 11 L29 20 L15 29Z" fill="#222"/></svg></div>
    <h4>Quisque dignissim</h4>
    <p>scelerisque mi tortor at ipsum cligula augue bibendum vestibulu</p>
    <span class="read">READ MORE</span>
  </article>
</section>

<div class="divider-band"></div>

<section class="highlights">
  <div class="ring" style="left:133px"><div class="ring-photo" role="img" aria-label="Touring motorbike on a mountain road" style="background:linear-gradient(180deg,#b9cde0 0%,#7e8c94 50%,#555 100%)"></div></div>
  <div class="highlight-text" style="left:352px">
    <h3>Oh yeah, it's that good<br>See for yourself.</h3>
    <p>Donec ullamcorper nulla non metus auctor fringilla. Vestibulum id ligula porta felis euismod semper. Praesent commodo cursus magna, vel scelerisque nisl consectetur. Fusce</p>
  </div>
  <div class="ring" style="left:599px"><div class="ring-photo" role="img" aria-label="Dirt bike rider on a gravel trail" style="background:linear-gradient(180deg,#6a8a5a 0%,#a8a494 55%,#d8d2c4 100%)"></div></div>
  <div class="highlight-text" style="left:814px">
    <h3>And lastly, this one.<br>Checkmate.</h3>
    <p>Donec ullamcorper nulla non metus auctor fringilla. Vestibulum id ligula porta felis euismod semper. Praesent commodo cursus magna, vel scelerisque nisl consectetur. Fusce</p>
  </div>
</section>

<section class="blogs">
  <h2>LATEST BLOGS</h2>
  <article class="post" style="top:1725px">
    <div class="post-photo" role="img" aria-label="Riders and bikes silhouetted against a sunset" style="background:linear-gradient(180deg,#f0a030 0%,#c0501a 55%,#2a1a10 100%)"></div>
    <h4>Mauris vel lacus vitae felis vestibulum</h4>
    <p>volutpat Etiam est nunc venenatis in tristique eu imperdiet ac nisl Cum sociis natoque penatibus et magnis dis parturient nascetur ridiculus</p>
    <span class="read">READ MORE</span>
  </article>
  <article class="post" style="top:1877px">
    <div class="post-photo" role="img" aria-label="Two motorbikes parked on a sandy road" style="background:linear-gradient(180deg,#d8b48a 0%,#b8885a 60%,#8a6040 100%)"></div>
    <h4>Donec dictum lectus non odio</h4>
    <p>volutpat Etiam est nunc venenatis in tristique eu imperdiet ac nisl Cum sociis natoque penatibus et magnis dis parturient nascetur ridiculus</p>
    <span class="read">READ MORE</span>
  </article>

  <aside class="gps">
    <div class="gps-head">GPS TRACKER</div>
    <div class="gps-map" role="img" aria-label="Map of Australia marking the riders' route stops"></div>
  </aside>
</section>

<footer class="site-footer">
  <div class="footer-col" style="left:160px"><h4>ABOUT</h4><ul><li>Aorttitor mattis</li><li>Enim In massa</li><li>Aibero</li><li>Interdum ne</li></ul></div>
  <div class="footer-col" style="left:331px"><h4>SUBLINKS</h4><ul><li>Donations</li><li>Our Map</li><li>Blogs</li><li>Video Feed</li></ul></div>
  <div class="footer-col" style="left:506px"><h4>RESOURCES</h4><ul><li>FAQ</li><li>Support</li><li>Testimonials</li><li>Contact</li></ul></div>
  <div class="footer-col" style="left:683px"><h4>CONTACT US</h4><ul>
    <li>48 Coastline Avenue</li>
    <li>PO Box 220 Bayview, NSW 2104</li>
    <li><svg width="11" height="11" viewBox="0 0 12 12"><path d="M2 1 L4.5 1 L5.5 4 L4 5 C5 7 6 8 7 8.5 L8 7 L11 8 L11 10.5 C11 11 10.5 11.5 10 11.5 C5 11 1 7 0.5 2 C0.5 1.5 1 1 2 1Z" fill="#fff"/></svg>(02) 5550 1842</li>
    <li><svg width="12" height="9" viewBox="0 0 12 9"><rect x="0" y="0" width="12" height="9" fill="#fff"/><path d="M0 0 L6 5 L12 0" fill="none" stroke="#3fb0aa" stroke-width="1.2"/></svg>hello@openroadride.org</li>
  </ul></div>
  <div class="footer-col" style="left:888px"><h4>FOLLOW US</h4><div class="social"><span></span><span></span><span></span><span></span></div></div>
</footer>

<div class="bottom-bar">© 2016 Company Name  All right reserved</div>

</body>
</html>
```